Trucking Company Website Design

We are working with a Trucking company in California. They provide trucking services for dirt, gravel, landscape bark, and landscape materials.

As you might imagine, there are no websites we could find for inspiration for trucking companies.

Thank you for taking the time to consider designing a website for us. We are web developers based in Stockton, CA, USA. Most of our projects go through the same process. Understanding this process may help you win a project with us. We custom-code all of our websites in-house. We don’t have any requirements as to what tools you use for your design, but we ask that you follow these guidelines.

IMAGES:
If you use any images or icons in the design, we ask that you have a link to the asset so we can purchase the image/icon. Most of the designs we submit do not have the customer’s images on them unless they have some great images. Be creative; show us the feeling you are trying to portray with your image choices. Use any royalty-free site you choose. We subscribe to Quillo and mainly use their images, but we can purchase images outside of Quillo. PLEASE NOTE: we will not submit designs to clients with watermarks on the images.

FONTS:
We ask that you identify the fonts you’re using in the design. This can be done in a message if you want. We typically use Varnex Fonts and Quillo Fonts.

CONTENT:
We're always open to different content and ideas. We often submit designs with stock images so the client can see our vision. We typically take pictures after the website launch to use their images with our vision. Lorem Ipsum is fine for paragraphs, but we ask that you make the Headers with correct English. We want to be able to show the vision and identify the sections of the website.

INSPIRATION:
We typically add a couple of links in the brief of websites we like to help you get started in your design.

REVISIONS:
We do not often ask for revisions of the designs unless we see something in the design that may not appeal to the client. If there are slight changes that we want to make, we do that in the development process.

FEEDBACK:
We rarely give feedback on designs during the design process. We are working on many website projects and do not have the time to provide feedback. We usually respond if your request is well thought out and asks specific questions, but a note asking “feedback, please” usually goes unanswered.

```html
<!DOCTYPE html>
<html lang="en">
<head>
<meta charset="utf-8">
<title>Ridgeline Haulage – Home</title>
<link href="https://fonts.googleapis.com/css2?family=Titillium+Web:wght@400;600;700&family=Poppins:wght@400;500;600&family=Roboto:wght@400;500&display=swap" rel="stylesheet">
<style>
:root{
  --blue:#1a7ab5;
  --red:#ef1a3a;
  --ink:#1b1b1b;
  --muted:#6b6b6b;
  --black:#000;
  --white:#fff;
}
*{box-sizing:border-box;margin:0;padding:0}
html,body{width:1200px;height:2940px;overflow:hidden;background:var(--white)}
body{position:relative;font-family:'Poppins',sans-serif;color:var(--ink)}
.abs{position:absolute}

/* header */
.site-header{position:absolute;left:0;top:0;width:1200px;height:114px;background:var(--white)}
.brand{position:absolute;left:97px;top:36px;display:flex;align-items:center;gap:12px;font-family:'Titillium Web',sans-serif;font-weight:700;font-size:34px;color:var(--blue);letter-spacing:.5px}
.brand-square{width:22px;height:22px;background:var(--red)}
.main-nav a{position:absolute;top:50px;font-size:14px;color:var(--ink);text-decoration:none}
.main-nav a.active{color:var(--red)}
.nav-marker{position:absolute;left:491px;top:22px;width:12px;height:12px;background:var(--red)}
.login-btn{position:absolute;left:993px;top:35px;width:108px;height:51px;background:var(--blue);color:var(--white);font-weight:600;font-size:14px;display:flex;align-items:center;justify-content:center}

/* hero */
.hero{position:absolute;left:0;top:114px;width:1200px;height:620px}
.hero-title-small{position:absolute;left:98px;top:150px;font-family:'Titillium Web',sans-serif;font-weight:700;font-size:40px;color:var(--white)}
.hero-title{position:absolute;left:98px;top:222px;font-family:'Titillium Web',sans-serif;font-weight:700;font-size:58px;color:var(--white);line-height:1}
.hero-title span{color:var(--blue)}
.btn-red{position:absolute;background:var(--red);color:var(--white);font-weight:600;font-size:14px;display:flex;align-items:center;justify-content:center;font-family:'Titillium Web',sans-serif}

/* section titles */
.section-title{position:absolute;width:1200px;left:0;text-align:center;font-family:'Titillium Web',sans-serif;font-weight:700;font-size:31px;color:var(--ink)}
.section-title span{color:var(--blue)}

/* services */
.service{position:absolute;width:256px;text-align:center}
.service-icon{width:104px;height:104px;margin:0 auto;border-radius:50%;background:var(--white);box-shadow:0 2px 12px rgba(0,0,0,.12);display:flex;align-items:center;justify-content:center}
.service-name{margin-top:22px;font-family:'Titillium Web',sans-serif;font-size:21px;color:var(--ink)}
.service-name.featured{color:var(--red)}
.service-text{margin-top:8px;font-size:13px;line-height:23px;color:var(--muted)}
.service-link{margin-top:15px;font-size:13px;font-weight:600;color:var(--red)}

/* about */
.about{position:absolute;left:0;top:1235px;width:1200px;height:510px;background:linear-gradient(90deg,#e9eaec,#f3f4f5 60%,#e6e7e9)}
.about h2{position:absolute;left:108px;top:72px;font-family:'Titillium Web',sans-serif;font-weight:700;font-size:31px}
.about h2 span{color:var(--blue)}
.about p{position:absolute;left:108px;top:148px;width:494px;font-size:12.6px;line-height:27.5px;color:#555;text-align:justify;hyphens:auto}
.about-photo{position:absolute;left:697px;top:60px;width:337px;height:393px;background:linear-gradient(160deg,#3d4a5c,#1f2733 60%,#141a22);clip-path:polygon(0 0,68% 0,100% 50%,68% 100%,0 100%,33% 50%)}

/* news */
.news-card{position:absolute;top:1943px;width:325px}
.news-photo{width:325px;height:202px}
.news-date{position:absolute;left:27px;top:179px;width:133px;height:44px;background:var(--blue);color:var(--white);font-size:14px;display:flex;align-items:center;justify-content:center}
.news-title{margin-top:49px;font-family:'Titillium Web',sans-serif;font-weight:600;font-size:20px;line-height:31px;color:var(--ink)}
.news-text{margin-top:12px;font-family:'Titillium Web',sans-serif;font-size:16px;line-height:26px;color:#777}
.news-link{margin-top:18px;font-family:'Titillium Web',sans-serif;font-weight:600;font-size:16px;color:var(--red)}

/* footer */
.footer-brand{position:absolute;left:98px;top:2702px;display:flex;align-items:center;gap:12px;font-family:'Titillium Web',sans-serif;font-weight:700;font-size:31px;color:var(--white)}
.footer-brand .brand-square{width:22px;height:22px;background:var(--white)}
.footer-heading{position:absolute;top:2636px;font-family:'Titillium Web',sans-serif;font-weight:600;font-size:20px;color:var(--white)}
.footer-links{position:absolute;left:472px;top:2675px;list-style:none;font-family:'Roboto',sans-serif;font-size:16px;line-height:26px;color:var(--white)}
.contact-item{position:absolute;left:653px;display:flex;gap:12px;font-family:'Roboto',sans-serif;font-size:14.5px;line-height:22px;color:var(--white)}
.newsletter{position:absolute;left:905px;top:2682px;width:196px;height:35px;background:var(--white);border-radius:4px;overflow:hidden}
.newsletter span{position:absolute;left:12px;top:9px;font-size:12px;color:#444;font-family:'Roboto',sans-serif}
.newsletter .send{position:absolute;right:0;top:0;width:47px;height:35px;background:var(--red);display:flex;align-items:center;justify-content:center}
.social{position:absolute;top:2757px;width:36px;height:36px;border-radius:50%;background:var(--blue)}
.copyright{position:absolute;left:0;top:2862px;width:1200px;text-align:center;font-family:'Roboto',sans-serif;font-size:14.5px;color:var(--white)}
</style>
</head>
<body>

<header class="site-header">
  <div class="brand"><span>RIDGELINE HAULAGE</span><span class="brand-square"></span></div>
  <span class="nav-marker"></span>
  <nav class="main-nav">
    <a class="active" style="left:476px">Home</a>
    <a style="left:565px">About Us</a>
    <a style="left:674px">Services</a>
    <a style="left:778px">Blog</a>
    <a style="left:857px">Contact Us</a>
  </nav>
  <div class="login-btn">LOG IN</div>
</header>

<section class="hero">
  <svg class="abs" style="left:0;top:0" width="1200" height="620" viewBox="0 0 1200 620">
    <defs>
      <linearGradient id="heroSky" x1="0" y1="0" x2="0" y2="1">
        <stop offset="0" stop-color="#3f5a7c"/>
        <stop offset=".35" stop-color="#c98a6a"/>
        <stop offset=".6" stop-color="#e8a35f"/>
        <stop offset="1" stop-color="#5a5560"/>
      </linearGradient>
    </defs>
    <polygon role="img" aria-label="Photo of a semi truck driving on a desert highway at sunset" points="0,0 1200,0 1200,474 600,590 0,474" fill="url(#heroSky)"/>
    <polygon points="0,474 600,590 1200,474 1200,495 600,617 0,495" fill="var(--red)"/>
    <circle cx="585" cy="553" r="5" fill="#fff"/>
    <circle cx="600" cy="553" r="5" fill="var(--blue)"/>
    <circle cx="615" cy="553" r="5" fill="#fff"/>
  </svg>
  <div class="hero-title-small">WELCOME TO</div>
  <div class="hero-title">RIDGELINE <span>HAULAGE</span></div>
  <div class="btn-red" style="left:99px;top:314px;width:138px;height:48px">GET STARTED</div>
</section>

<h2 class="section-title" style="top:822px">OUR <span>SERVICES</span></h2>

<svg class="abs" style="left:0;top:955px" width="1200" height="4">
  <line x1="270" y1="2" x2="932" y2="2" stroke="#999" stroke-width="1.5" stroke-dasharray="2 4"/>
</svg>

<div class="service" style="left:89px;top:903px">
  <div class="service-icon">
    <svg width="52" height="52" viewBox="0 0 52 52" fill="none" stroke="var(--blue)" stroke-width="2"><path d="M16 18c4-6 12-2 16-5s8 4 4 8 2 9-4 12-10 8-14 3-8-4-4-9-2-5 2-9z"/><circle cx="9" cy="10" r="3"/><circle cx="44" cy="42" r="2.5"/><circle cx="40" cy="9" r="2"/></svg>
  </div>
  <div class="service-name">Dirt</div>
  <div class="service-text">Lorem ipsum dolor sit amet,<br>consectetur adipiscing elit,</div>
  <div class="service-link">Learn More</div>
</div>
<div class="service" style="left:345px;top:903px">
  <div class="service-icon">
    <svg width="52" height="52" viewBox="0 0 52 52" fill="none" stroke="var(--red)" stroke-width="2"><path d="M26 6 L46 40 H6 Z"/><path d="M20 40v8M32 40v8"/><circle cx="24" cy="26" r="2"/><circle cx="30" cy="32" r="2"/><circle cx="20" cy="34" r="1.5"/></svg>
  </div>
  <div class="service-name featured">Gravel</div>
  <div class="service-text">Lorem ipsum dolor sit amet,<br>consectetur adipiscing elit,</div>
  <div class="service-link">Learn More</div>
</div>
<div class="service" style="left:600px;top:903px">
  <div class="service-icon">
    <svg width="64" height="40" viewBox="0 0 64 40" fill="none" stroke="var(--blue)" stroke-width="2"><path d="M4 26v-8l10-2 8-8h18l10 8 10 2v8z"/><circle cx="16" cy="27" r="5"/><circle cx="48" cy="27" r="5"/></svg>
  </div>
  <div class="service-name">Landscape Bark</div>
  <div class="service-text">Lorem ipsum dolor sit amet,<br>consectetur adipiscing elit,</div>
  <div class="service-link">Learn More</div>
</div>
<div class="service" style="left:856px;top:903px">
  <div class="service-icon">
    <svg width="56" height="52" viewBox="0 0 56 52" fill="none" stroke="var(--blue)" stroke-width="2"><path d="M4 18h32l-4 20H8z"/><circle cx="12" cy="44" r="4"/><circle cx="30" cy="44" r="4"/><circle cx="42" cy="16" r="8"/><circle cx="42" cy="16" r="3"/><path d="M12 18l4-8 6 8"/></svg>
  </div>
  <div class="service-name">Landscape Materials</div>
  <div class="service-text">Lorem ipsum dolor sit amet,<br>consectetur adipiscing elit,</div>
  <div class="service-link">Learn More</div>
</div>

<section class="about">
  <h2>ABOUT <span>US</span></h2>
  <p>Sed ut perspiciatis unde omnis iste natus error sit voluptatem accusantium doloremque laudantium, totam rem aperiam, eaque ipsa quae ab illo inventore veritatis et quasi architecto beatae vitae dicta sunt explicabo. Nemo enim ipsam voluptatem quia voluptas sit aspernatur aut odit aut fugit, sed quia consequuntur magni dolores eos qui ratione voluptatem sequi nesciunt. Neque porro quisquam est, qui non numquam eius modi tempora incidunt ut labore et dolore magnam aliquam quaerat voluptatem.</p>
  <div class="btn-red" style="left:108px;top:373px;width:139px;height:48px">LEARN MORE</div>
  <div class="about-photo" role="img" aria-label="Photo of a dark semi truck parked at a loading dock at dusk"></div>
</section>

<h2 class="section-title" style="top:1857px">LATEST <span>NEWS</span></h2>

<article class="news-card" style="left:96px">
  <div class="news-photo" role="img" aria-label="Photo of a silver truck on a highway" style="background:linear-gradient(180deg,#5d6e58,#8b8f95 55%,#4b4f55)"></div>
  <div class="news-date">20 June,2023</div>
  <div class="news-title">Sed ut perspiciatis unde omnis iste error sit voluptatem</div>
  <div class="news-text">Lorem ipsum dolor sit amet, consectetur adipiscing elit, sed do eiusmod tempor</div>
  <div class="news-link">READ MORE</div>
</article>
<article class="news-card" style="left:436px">
  <div class="news-photo" role="img" aria-label="Photo of a white truck on a desert road under a pink sky" style="background:linear-gradient(180deg,#b9a9c8,#e6b9a6 45%,#6f6a6c)"></div>
  <div class="news-date">20 June,2023</div>
  <div class="news-title">Sed ut perspiciatis unde omnis iste error sit voluptatem</div>
  <div class="news-text">Lorem ipsum dolor sit amet, consectetur adipiscing elit, sed do eiusmod tempor</div>
  <div class="news-link">READ MORE</div>
</article>
<article class="news-card" style="left:776px">
  <div class="news-photo" role="img" aria-label="Photo of a row of white trucks parked in a depot" style="background:linear-gradient(180deg,#cfc9c2,#b7aea3 55%,#57524d)"></div>
  <div class="news-date">20 June,2023</div>
  <div class="news-title">Sed ut perspiciatis unde omnis iste error sit voluptatem</div>
  <div class="news-text">Lorem ipsum dolor sit amet, consectetur adipiscing elit, sed do eiusmod tempor</div>
  <div class="news-link">READ MORE</div>
</article>

<footer>
  <svg class="abs" style="left:0;top:2458px" width="1200" height="482" viewBox="0 0 1200 482">
    <polygon points="0,122 600,0 1200,122 1200,482 0,482" fill="var(--red)"/>
    <polygon points="0,145 600,18 1200,145 1200,482 0,482" fill="var(--black)"/>
  </svg>
  <div class="footer-brand"><span>RIDGELINE HAULAGE</span><span class="brand-square"></span></div>

  <div class="footer-heading" style="left:472px">QUICK LINKS</div>
  <ul class="footer-links">
    <li>Home</li><li>About Us</li><li>Services</li><li>Blog</li><li>Contact Us</li>
  </ul>

  <div class="footer-heading" style="left:653px">CONTACT US</div>
  <div class="contact-item" style="top:2683px">
    <svg width="16" height="20" viewBox="0 0 16 20"><path d="M8 0a7 7 0 0 0-7 7c0 5 7 13 7 13s7-8 7-13a7 7 0 0 0-7-7zm0 10a3 3 0 1 1 0-6 3 3 0 0 1 0 6z" fill="#fff"/></svg>
    <span>Lorem ipsum dolor sit<br>amet, consectetur</span>
  </div>
  <div class="contact-item" style="top:2747px">
    <svg width="16" height="16" viewBox="0 0 16 16"><path d="M3 1l3 3-2 2c1 2 3 4 5 5l2-2 3 3-2 3C6 15 1 10 1 3z" fill="#fff"/></svg>
    <span>+1 (555) 010 0199</span>
  </div>
  <div class="contact-item" style="top:2786px">
    <svg width="16" height="16" viewBox="0 0 16 16"><path d="M1 3h14v10H1z" fill="#fff"/><path d="M1 3l7 6 7-6" stroke="#000" stroke-width="1.3" fill="none"/></svg>
    <span>info@ridgelinehaulage.com</span>
  </div>

  <div class="footer-heading" style="left:905px">NEWSLETTER</div>
  <div class="newsletter">
    <span>Ener email</span>
    <div class="send"><svg width="14" height="11" viewBox="0 0 14 11"><path d="M0 0h14v11H0z" fill="#fff"/><path d="M0 0l7 6 7-6" stroke="var(--red)" stroke-width="1.4" fill="none"/></svg></div>
  </div>
  <span class="social" style="left:914px"></span>
  <span class="social" style="left:962px"></span>
  <span class="social" style="left:1010px"></span>
  <span class="social" style="left:1058px"></span>

  <div class="copyright">©Copyrights 2023 Ridgeline Haulage &nbsp;&nbsp;| &nbsp;&nbsp;All Rights Reserved</div>
</footer>

</body>
</html>
```